Custom unique Stationary design for Logistics company

We need a custom, unique , elegant and luxurious full stationary design using our new logo, following these guidelines:
1- Business card: double sided, both sides uses the navy blue as the background main color (same as the code of the navy blue used in our logo).
2- envelope and folder: also use the same navy blue as the main background color.
3- book cover( notepad cover) : same thing with the navy blue
4- letterhead: feel free to use the combination of the colors in our logo.
5- rest of the items are up to your creativity

Target Market(s)

corporates and other businesses

Industry/Entity Type

Logistics and heavy machines contractors

Requirements
Must have
• Letterhead, business card, envelope, notepad cover, paper, file
Nice to have
• navy blue to be main background color for business card, envelope, notepad cover

```html
<!DOCTYPE html>
<html lang="en">
<head>
<meta charset="utf-8">
<title>Harborline Freight – Envelope</title>
<link href="https://fonts.googleapis.com/css2?family=Montserrat:wght@500;700&display=swap" rel="stylesheet">
<style>
  :root {
    --navy: #074d6f;
    --orange: #e85a2c;
    --paper: #f4f3f3;
    --backdrop: #d0d0d0;
    --ink: #1c1c1c;
  }
  * { margin: 0; padding: 0; box-sizing: border-box; }
  html, body { width: 1200px; height: 1050px; overflow: hidden; }
  body {
    background: var(--backdrop);
    font-family: "Montserrat", Arial, sans-serif;
    position: relative;
  }
  .envelope {
    position: absolute;
    left: 145px;
    width: 910px;
    height: 390px;
    background: var(--paper);
    overflow: hidden;
  }
  .envelope--back { top: 105px; }
  .envelope--front { top: 556px; }

  .flap {
    position: absolute;
    top: 0; left: 0;
    width: 910px; height: 131px;
  }
  .flap__name {
    position: absolute;
    top: 0; left: 0; width: 910px; height: 131px;
    display: flex; align-items: center; justify-content: center; gap: 10px;
    color: #fff;
    font-weight: 700;
    font-size: 30px;
    letter-spacing: 1px;
  }
  .brand-dot {
    width: 14px; height: 14px; border-radius: 50%;
    background: currentColor;
    flex: none;
  }

  .sender {
    position: absolute;
    left: 41px; top: 58px;
  }
  .sender__name {
    display: flex; align-items: center; gap: 12px;
    color: var(--navy);
    font-weight: 700;
    font-size: 36px;
    letter-spacing: 0.5px;
    height: 110px;
  }
  .sender__name .brand-dot { width: 18px; height: 18px; }
  .sender__address {
    margin-top: 18px;
    font-style: normal;
    font-weight: 500;
    font-size: 15px;
    line-height: 20px;
    color: var(--ink);
  }

  .footer-bands {
    position: absolute;
    left: 0; bottom: 0;
    width: 910px;
  }
  .footer-bands__accent {
    height: 9px;
    background: var(--orange);
    margin-bottom: 6px;
  }
  .footer-bands__base {
    height: 46px;
    background: var(--navy);
  }
</style>
</head>
<body>

  <section class="envelope envelope--back">
    <svg class="flap" viewBox="0 0 910 131" aria-hidden="true">
      <path fill="var(--navy)" d="M0 0 H910 L886 92 Q872 131 828 131 H82 Q38 131 24 92 Z"/>
    </svg>
    <div class="flap__name"><span class="brand-dot"></span>Harborline Freight</div>
  </section>

  <section class="envelope envelope--front">
    <div class="sender">
      <div class="sender__name"><span class="brand-dot"></span>Harborline Freight</div>
      <address class="sender__address">
        1420 Harbor Line Ave, Suite 310<br>
        Fairview, ON K7A&nbsp;&nbsp;3M2
      </address>
    </div>
    <div class="footer-bands" aria-hidden="true">
      <div class="footer-bands__accent"></div>
      <div class="footer-bands__base"></div>
    </div>
  </section>

</body>
</html>
```